Hollow Meridian Book website design.

This is a simple one-page web design for my book.
I have all files and video needed.
Domain listed with Net Harbor.
Password and username will be given to winning bid.
Domain address, www.hollowmeridian.info
Upload a 30 second video so it can be played on the website.
Book cover photo
Book Blurb text.
Links to Rivermart and Audio books where the book can be purchased.
Below is the link to the Rivermart listing.
https://www.rivermart.example/dp/X00AAAAAA1/?coliid=QWERTYUIOPASD&colid=1ZXCVBNMLKJH0&psc=0&ref_=lv_ov_lig_dp_i
Below is the link to my Listenly books.com listing.
https://www.listenly.example/pd/Hollow-Meridian-Audiobook/X00BBBBBB2?qid=1000000001&sr=1-7&ref=a_search_c3_lProduct_1_7&pf_rd_p=00000000-aaaa-bbbb-cccc-000000000000&pf_rd_r=ZZZZ00000000000000QQ
Text on page.” Click on either logo to go directly to Rivermart or Listenly.com
Link Listenly book logo to my book on Listenly.com
Place this text under Listenly.com logo: “Free to new members of Listenly.com”
Link Rivermart logo to my book on Rivermart.
Place this text under Rivermart logo “ Free to new Pagewisp members on Rivermart.com”
Link the book photo to the Rivermart.com web address as well.
Enter meta tags or keywords below for search engines to locate webpage.
Hollow Meridian
Conspiracy
Conspiracy Books
Spy books
Thriller books
Suspense books
Comedy books
Dorian Welbeck

```html
<!DOCTYPE html>
<html lang="en">
<head>
<meta charset="utf-8">
<title>Hollow Meridian — A Novel by Dorian Welbeck</title>
<meta name="keywords" content="Hollow Meridian, Conspiracy, Conspiracy Books, Spy books, Thriller books, Suspense books, Comedy books, Dorian Welbeck">
<link href="https://fonts.googleapis.com/css2?family=Lato:wght@700;900&family=Poppins:wght@400;500;600&display=swap" rel="stylesheet">
<style>
:root{
  --red:#e3141c;
  --navy:#0d1a6b;
  --ink:#111111;
  --text:#1d1d1d;
  --white:#ffffff;
  --hero-a:#3b3cab;
  --hero-b:#24288a;
  --circle-top:#1b1a78;
  --circle-mid:#5a1248;
  --circle-bot:#e0101c;
}
*{margin:0;padding:0;box-sizing:border-box}
html,body{width:1200px;height:2301px;overflow:hidden}
body{position:relative;background:var(--white);font-family:'Poppins',sans-serif;color:var(--text)}
a{color:inherit;text-decoration:none}
.abs{position:absolute}

/* header */
.site-header{position:absolute;left:0;top:0;width:1200px;height:85px;background:var(--white);z-index:3}
.brand{position:absolute;left:112px;top:14px;line-height:1}
.brand-top{display:block;font-family:'Poppins',sans-serif;font-weight:600;font-size:29px;color:var(--red);letter-spacing:1px}
.brand-bottom{display:block;font-family:'Poppins',sans-serif;font-weight:500;font-size:18px;color:var(--ink);letter-spacing:5.6px;margin-top:3px}
.main-nav a{position:absolute;top:34px;font-size:15.5px;color:#222}
.main-nav a.active{color:var(--red)}
.account{position:absolute;left:792px;top:28px;display:flex;align-items:center;gap:10px;font-size:15.5px;color:#222}
.btn-login{position:absolute;left:943px;top:21px;width:147px;height:42px;border:2.5px solid var(--navy);border-radius:22px;display:flex;align-items:center;justify-content:center;font-weight:500;font-size:14.5px;color:var(--ink)}

/* hero */
.hero{position:absolute;left:0;top:85px;width:1200px}
.hero-title{position:absolute;left:108px;top:258px;font-family:'Lato',sans-serif;font-weight:700;font-size:43px;line-height:44px;color:var(--white)}
.hero-sub{position:absolute;left:110px;top:362px;font-size:15.5px;font-weight:500;color:var(--white)}
.btn-video{position:absolute;left:110px;top:402px;width:214px;height:46px;border-radius:23px;background:var(--white);display:flex;align-items:center;padding-left:25px;font-size:15.5px;font-weight:500;color:var(--ink)}
.btn-video .play{position:absolute;right:0;top:0;width:46px;height:46px;border-radius:50%;background:var(--red)}

/* book sections */
.cover-art{position:absolute}
.book-title{position:absolute;font-family:'Lato',sans-serif;font-weight:700;font-size:30px;color:var(--ink);letter-spacing:-.2px}
.book-title span{color:var(--red)}
.blurb-label{position:absolute;font-family:'Lato',sans-serif;font-weight:700;font-size:21px;color:var(--ink)}
.blurb{position:absolute;width:461px;height:180px;overflow:hidden;font-size:15.2px;line-height:25.7px;text-align:justify;color:#222}
.store-name{position:absolute;font-family:'Poppins',sans-serif;font-weight:600;color:var(--white)}
.store-badge{position:absolute;background:var(--ink);display:flex;align-items:center;justify-content:center}
.store-link{position:absolute;font-size:15.5px;color:var(--red);border-bottom:1px solid var(--red);padding-bottom:1px}

/* footer */
.footer-art{position:absolute;left:0;top:1840px}
.footer-brand{position:absolute;left:0;width:1200px;top:2008px;text-align:center;color:var(--white);line-height:1}
.footer-brand .brand-top{color:var(--white);font-size:30px}
.footer-brand .brand-bottom{color:var(--white);letter-spacing:6.5px;margin-top:6px}
.contact-row{position:absolute;top:2097px;left:0;width:1200px;height:32px;color:var(--white);font-size:15.5px}
.contact-row .item{position:absolute;top:0;height:32px;display:flex;align-items:center;gap:10px}
.ring{width:31px;height:31px;border:1.6px solid var(--white);border-radius:50%;display:flex;align-items:center;justify-content:center}
.divider{position:absolute;width:1.5px;background:var(--white)}
.footer-nav a{position:absolute;top:2161px;font-size:15.5px;color:var(--white);transform:translateX(-50%)}
.footer-rule{position:absolute;left:112px;top:2218px;width:976px;height:1px;background:rgba(255,255,255,.7)}
.copyright{position:absolute;top:2240px;left:0;width:1200px;text-align:center;font-size:15.5px;color:var(--white)}
</style>
</head>
<body>

<header class="site-header">
  <a class="brand" href="#">
    <span class="brand-top">HOLLOW</span>
    <span class="brand-bottom">MERIDIAN</span>
  </a>
  <nav class="main-nav">
    <a class="active" href="#" style="left:440px">Home</a>
    <a href="#" style="left:519px">About</a>
    <a href="#" style="left:597px">Our Book</a>
    <a href="#" style="left:700px">Contact</a>
  </nav>
  <a class="account" href="#">
    <svg width="28" height="28" viewBox="0 0 28 28" fill="none" stroke="#111" stroke-width="1.8"><circle cx="14" cy="14" r="12.5"/><circle cx="14" cy="11" r="4.5"/><path d="M6 22.5c2-4 5-5.5 8-5.5s6 1.5 8 5.5"/></svg>
    My account
  </a>
  <a class="btn-login" href="#">LOG IN</a>
</header>

<section class="hero">
  <svg width="1200" height="640" viewBox="0 0 1200 640" role="img" aria-label="Photo of a smiling man in a suit raising both arms before a blue flag with gold stars">
    <defs>
      <linearGradient id="heroFill" x1="0" y1="0" x2="1" y2="1">
        <stop offset="0" stop-color="var(--hero-a)"/>
        <stop offset="1" stop-color="var(--hero-b)"/>
      </linearGradient>
    </defs>
    <path d="M0 0H1200V635C1120 600 1020 555 880 550C700 545 520 600 360 595C220 592 100 575 0 540Z" fill="url(#heroFill)"/>
    <path d="M640 548C760 528 880 520 960 535C1060 553 1140 590 1200 635V610C1130 570 1060 538 960 525C860 512 750 520 640 548Z" fill="var(--navy)"/>
  </svg>
  <h1 class="hero-title abs" style="top:173px">Welcome To The<br>Hollow Meridian</h1>
  <p class="hero-sub" style="top:277px">The Powers That Be Here In America</p>
  <a class="btn-video" href="#" style="top:317px">Watch our video
    <span class="play"><svg width="46" height="46" viewBox="0 0 46 46"><path d="M18 14L31 23L18 32Z" fill="#fff"/></svg></span>
  </a>
</section>

<!-- first book -->
<a class="cover-art" href="https://www.rivermart.example/dp/X00AAAAAA1/?coliid=QWERTYUIOPASD&colid=1ZXCVBNMLKJH0&psc=0&ref_=lv_ov_lig_dp_i" style="left:108px;top:770px">
  <svg width="420" height="500" viewBox="0 0 420 500" role="img" aria-label="Hardcover of Hollow Meridian by Dorian Welbeck, a man's profile over a flag and government building">
    <defs>
      <linearGradient id="ringA" x1="0" y1="0" x2="0" y2="1">
        <stop offset="0" stop-color="var(--circle-top)"/>
        <stop offset=".55" stop-color="var(--circle-mid)"/>
        <stop offset="1" stop-color="var(--circle-bot)"/>
      </linearGradient>
      <linearGradient id="coverA" x1="0" y1="0" x2="1" y2="1">
        <stop offset="0" stop-color="#27305a"/>
        <stop offset=".5" stop-color="#5a1a22"/>
        <stop offset="1" stop-color="#0c0c0c"/>
      </linearGradient>
    </defs>
    <circle cx="209" cy="248" r="208" fill="url(#ringA)"/>
    <path d="M42 20L375 8L357 400L57 497Z" fill="url(#coverA)"/>
  </svg>
</a>
<h2 class="book-title" style="left:610px;top:845px">HOLLOW <span>MERIDIAN</span></h2>
<h3 class="blurb-label" style="left:610px;top:890px">Book Blurb</h3>
<p class="blurb" style="left:610px;top:929px">A fictional novel based on current events surrounding the covid 19 virous. Jack Holman is a well-respected independent journalist contracted by the Harbor Ledger, upon his return from reporting on the war in Syria he is tasked to investigate the covid virus outbreak in China. As he digs deeper, he uncovers a hideous plot by the powers that be here in America. Jack risks life and limb to uncover the truth before it is too late.</p>
<a class="store-badge" href="https://www.rivermart.example/dp/X00AAAAAA1/?coliid=QWERTYUIOPASD&colid=1ZXCVBNMLKJH0&psc=0&ref_=lv_ov_lig_dp_i" style="left:612px;top:1125px;width:114px;height:52px">
  <span class="store-name" style="position:static;font-size:18px">Rivermart</span>
</a>
<a class="store-link" href="https://www.rivermart.example/dp/X00AAAAAA1/?coliid=QWERTYUIOPASD&colid=1ZXCVBNMLKJH0&psc=0&ref_=lv_ov_lig_dp_i" style="left:740px;top:1138px">Free to new Pagewisp members on Rivermart.com</a>

<!-- second book -->
<h2 class="book-title" style="left:108px;top:1408px">HOLLOW <span>MERIDIAN</span></h2>
<h3 class="blurb-label" style="left:108px;top:1453px">Book Blurb</h3>
<p class="blurb" style="left:108px;top:1492px">A fictional novel based on current events surrounding the covid 19 virous. Jack Holman is a well-respected independent journalist contracted by the Harbor Ledger, upon his return from reporting on the war in Syria he is tasked to investigate the covid virus outbreak in China. As he digs deeper, he uncovers a hideous plot by the powers that be here in America. Jack risks life and limb to uncover the truth before it is too late.</p>
<a href="https://www.listenly.example/pd/Hollow-Meridian-Audiobook/X00BBBBBB2?qid=1000000001&sr=1-7&ref=a_search_c3_lProduct_1_7&pf_rd_p=00000000-aaaa-bbbb-cccc-000000000000&pf_rd_r=ZZZZ00000000000000QQ" class="abs" style="left:111px;top:1700px;font-weight:600;font-size:30px;color:var(--ink);line-height:1">Listenly</a>
<a class="store-link" href="https://www.listenly.example/pd/Hollow-Meridian-Audiobook/X00BBBBBB2?qid=1000000001&sr=1-7&ref=a_search_c3_lProduct_1_7&pf_rd_p=00000000-aaaa-bbbb-cccc-000000000000&pf_rd_r=ZZZZ00000000000000QQ" style="left:255px;top:1711px">Free to new members of Listenly.com</a>
<a class="cover-art" href="https://www.rivermart.example/dp/X00AAAAAA1/?coliid=QWERTYUIOPASD&colid=1ZXCVBNMLKJH0&psc=0&ref_=lv_ov_lig_dp_i" style="left:668px;top:1320px">
  <svg width="420" height="500" viewBox="0 0 420 500" role="img" aria-label="Hardcover of Hollow Meridian by Dorian Welbeck, black cover with a man's profile in monochrome">
    <defs>
      <linearGradient id="ringB" x1="0" y1="0" x2="0" y2="1">
        <stop offset="0" stop-color="var(--circle-top)"/>
        <stop offset=".55" stop-color="var(--circle-mid)"/>
        <stop offset="1" stop-color="var(--circle-bot)"/>
      </linearGradient>
      <linearGradient id="coverB" x1="0" y1="0" x2="0" y2="1">
        <stop offset="0" stop-color="#050505"/>
        <stop offset=".6" stop-color="#1c1c1c"/>
        <stop offset="1" stop-color="#3a3a3a"/>
      </linearGradient>
    </defs>
    <circle cx="210" cy="247" r="208" fill="url(#ringB)"/>
    <path d="M43 20L376 8L357 420L58 497Z" fill="url(#coverB)"/>
  </svg>
</a>

<!-- footer -->
<footer>
  <svg class="footer-art" width="1200" height="461" viewBox="0 1840 1200 461">
    <path d="M0 1845C260 1985 560 1960 960 1884L960 2010L0 2010Z" fill="var(--red)"/>
    <path d="M0 1898C300 1985 600 1935 900 1890C1030 1872 1140 1905 1200 1938V2301H0Z" fill="var(--navy)"/>
  </svg>
  <div class="footer-brand">
    <span class="brand-top">HOLLOW</span>
    <span class="brand-bottom">MERIDIAN</span>
  </div>
  <div class="contact-row">
    <a class="item" href="#" style="left:246px"><span class="ring"></span></a>
    <a class="item" href="#" style="left:285px"><span class="ring"></span></a>
    <a class="item" href="#" style="left:324px"><span class="ring"></span></a>
    <span class="divider" style="left:400px;top:5px;height:22px"></span>
    <a class="item" href="mailto:hello@hollowmeridian.info" style="left:429px">
      <span class="ring"><svg width="16" height="12" viewBox="0 0 16 12" fill="none" stroke="#fff" stroke-width="1.5"><rect x="1" y="1" width="14" height="10" rx="1"/><path d="M1 1.5L8 7L15 1.5"/></svg></span>
      hello@hollowmeridian.info
    </a>
    <span class="divider" style="left:741px;top:5px;height:22px"></span>
    <a class="item" href="tel:+15550142277" style="left:772px">
      <span class="ring"><svg width="14" height="14" viewBox="0 0 24 24" fill="#fff"><path d="M6.6 10.8a15.1 15.1 0 006.6 6.6l2.2-2.2a1 1 0 011-.25 11.4 11.4 0 003.6.57 1 1 0 011 1V20a1 1 0 01-1 1A17 17 0 013 4a1 1 0 011-1h3.5a1 1 0 011 1c0 1.25.2 2.45.57 3.57a1 1 0 01-.25 1z"/></svg></span>
      +1(555) 014 2277
    </a>
  </div>
  <nav class="footer-nav">
    <a href="#" style="left:398px">Home</a>
    <a href="#" style="left:519px">About</a>
    <a href="#" style="left:651px">Our Book</a>
    <a href="#" style="left:791px">Contact</a>
  </nav>
  <span class="divider" style="left:457px;top:2159px;height:26px"></span>
  <span class="divider" style="left:589px;top:2161px;height:26px"></span>
  <span class="divider" style="left:715px;top:2161px;height:26px"></span>
  <div class="footer-rule"></div>
  <p class="copyright">Copyrights@2022Hollowmeridian.. All Rights Reserved</p>
</footer>

</body>
</html>
```